Velvet Ladle Wishes Website Design; Cupcake Business with a unique and bespoke design element

We need a website design for a new bespoke and unique business making gourmet cupcakes - but MOST IMPORTANTLY we design and handmake cupcake wrappers and toppers specifically for each client's event. We are based in Sydney, Australia. The final resulting website should be elegant yet whimsical reflecting the notion of dreams and very elegant events eg weddings and very special parties.

We want to eventually have about 5 pages, HOWEVER, this project is specifically for the first page (ie Home page) and one other only. The final required pages are: a HOME page; ABOUT US page; PHOTO GALLERY page; FLAVOUR MENU & OTHER PRODUCTS page; CONTACT & INTERNET ENQUIRY page.

We expect the HOME page to be quite elaborate, perhaps including some animation. We will be providing the text content for all the other pages, and basically they will have the same background as the home page. We are looking for a clean design that runs across each page thus giving the website a continuity that pulls it all together. We would like our logo to be included on each page.

PLEASE NOTE: We will want multiple pages worked on in the handover phase but initially we want a very concise, consistent template to limit the amount of work to prospective designers.

While we are primarily looking for the design phase to be covered by this project, we would certainly appreciate coding to be included and will take that into consideration when choosing a winner.
Updates

Hi Designers

We have added some more information to our brief - please review it.

Thanks and happy designing

Hi Designers

Please note that we have increased our Prize money to $750.00.  We hope this encourages you to participate.

Thanks and regards
Velvet Ladle Wishes

Hi Designers

We've just posted some photos to help give you an idea of what we do.  Please note our attention to detail and precision in our work.

Thanks
Velvet Ladle Wishes

Hi Designers

Please Note:  What makes us different  to any other cupcake business is that we design cupcake wrappers and toppers, unique to our client's event whether it be a wedding, a birthday party or product launch.  We consult with our client to understand themes, colours, styles etc.  We then have our designs printed, next they are cut by a specialised computerised cutting machine,  We assemble everything by hand, and usually embellish the wrapper and topper with pearls, crystals, feathers, lace, ribbons or whatever else is appropriate for the event.  All work is totally bespoke, unique and individual.  No other cupcake supplier that we know of goes to these lengths to satisfy their client's dreams.

THE WRAPPER AND TOPPER IS OUR PRIMARY SELLING POINT. 

PLEASE NOTE:- We have uploaded a new photograph which we want to be used as the main photograph on the landing page.

We have removed all previous photographs of cupcakes (except for one that we can't get rid of).

We don't want a picture of a cupcake on the landing page we want the image _D7C3239.jpg to be used for that purpose.

We have also uploaded our logo in a number of file formats as we have had requests from you for these.

Hi designers

we have a crazy busy weekend on and won't be able to make any decisions re our competition until Monday  -  sorry to keep you in suspense, just a couple more days please!

regards
Pam

Target Market(s)

Primarily women - brides, new mothers (Christenings), Event Planners, who place an emphasis on the beauty of a product rather than the cost

Industry/Entity Type

Events

Requirements
Must have
• It must have our Logo (see attached upload) on each page (our logo is a butterfly atop a cupcake resting on a spoon and our motto is "Creating Delicious Works of Art". The colours used are pale pink, blue and chocolate brown and we'd expect these colours to be repeated in the final website.
The website must have a photo gallery which we can access and add to/change as our business grows.
We need a contact page which has an "internet enquiry form".
There should be a "Menu" page describing our cupcake flavours.
The Home page must have a party/event feel to it - definitely making an enquirer want to enter further into the site.
Nice to have
• Our logo is attached below in the "uploads". One idea that we have had is to use the butterfly in the logo but start it as a caterpillar crawling on the screen; as it spins it's cocoon the words "Sweet Dreams Little Caterpillar" would appear on screen; this would incorporate the "Dreams" in our Business Name; then our logo butterfly would hatch. This encapsulates the idea of taking something plain (caterpillar/cupcake) and creating something beautiful (butterfly/OUR cupcake).
However, we are open to other design ideas.
The colours we would like to have are pale pink, blue and chocolate brown in the design.

Some websites we really admire are: www.mirabellhart.com www.ribbonglitterloaf.com.au and www.greetingsoriel.com.au
These websites have a lightness and sense of fantasy to them. They do not convey a corporate image at all, rather they make you want to be at the party.
Should not have
• No "Corporate" style.

Most Important: We already have a website which we are not happy with - that is why we are going through this exercise to replace it. That means we DO NOT want anything along the lines of our current website. We are expecting some fresh ideas for our prize money.

```html
<!DOCTYPE html>
<html lang="en">
<head>
<meta charset="utf-8">
<title>Velvet Ladle Wishes – Home</title>
<link href="https://fonts.googleapis.com/css2?family=Cabin:wght@400;500;600&family=Parisienne&family=Fondamento&display=swap" rel="stylesheet">
<style>
  :root{
    --bg-pink:#f6cdd3;
    --page-pink:#fbdde1;
    --band-pink:#fbbcc3;
    --choc:#5a3a40;
    --choc-dark:#4d2c33;
    --choc-light:#6d464e;
    --blue:#2f6a96;
    --sky:#66a2c8;
    --rose:#f8adb4;
    --hot-pink:#e2206a;
    --brown-text:#5b2b0c;
    --logo-brown:#5a3320;
    --body-text:#4a3333;
    --white:#ffffff;
  }
  *{box-sizing:border-box;margin:0;padding:0}
  html,body{width:1200px;height:1025px;overflow:hidden}
  body{position:relative;background:var(--bg-pink);font-family:"Cabin",sans-serif;color:var(--body-text)}
  .page{position:absolute;left:155px;top:0;width:890px;height:1025px;background:var(--page-pink)}
  .header-bg{position:absolute;left:155px;top:95px;width:890px;height:300px;background:linear-gradient(#f8c3cb,#fbd0d6)}

  .search{position:absolute;top:13px;left:773px;display:flex;align-items:center;font-size:14px;color:#5c4a4e}
  .search input{margin-left:14px;width:165px;height:24px;border:1px solid #8a6f75;background:#a88c93}
  .search button{margin-left:4px;width:28px;height:24px;border:0;background:#5ea6d8;color:var(--white);font:14px "Cabin",sans-serif}

  .nav-tail{position:absolute;top:64px;width:86px;height:42px;background:var(--choc-dark)}
  .nav-tail.left{left:70px;clip-path:polygon(0 50%,12% 0,100% 0,100% 100%,12% 100%)}
  .nav-tail.right{left:1044px;clip-path:polygon(0 0,88% 0,100% 50%,88% 100%,0 100%)}
  .nav{position:absolute;left:122px;top:52px;width:956px;height:44px;background:var(--choc);border:3px solid var(--choc-dark);box-shadow:0 6px 8px rgba(80,40,50,.35)}
  .nav ul{list-style:none;position:absolute;left:0;top:0;width:100%;height:100%}
  .nav li{position:absolute;top:7px;font-family:"Fondamento",cursive;font-size:14px;color:#f4e6e8;padding:2px 18px}
  .nav li.active{background:#3a1f24;border-radius:2px}

  .logo{position:absolute;left:218px;top:300px;display:flex;align-items:center;gap:14px}
  .logo-dot{width:34px;height:34px;border-radius:50%;background:var(--logo-brown)}
  .logo-name{font-family:"Cabin",sans-serif;font-weight:500;font-size:42px;color:var(--logo-brown);line-height:1}
  .hero-art{position:absolute;left:762px;top:255px;width:255px;height:170px;border-radius:50%;background:radial-gradient(ellipse at 45% 40%,#fff8f4,#f4d6d6 55%,#c2303a 90%)}

  .scallop{position:absolute;left:147px;top:384px}

  .welcome{position:absolute;left:178px;top:497px;font-family:"Parisienne",cursive;font-weight:400;font-size:30px;color:var(--blue)}
  .lead-pink{position:absolute;left:179px;top:550px;font-size:12px;color:var(--hot-pink)}
  .lead-brown{position:absolute;left:179px;top:569px;font-size:12px;color:var(--brown-text)}
  .intro{position:absolute;left:179px;top:595px;width:548px;font-size:11px;line-height:16px}
  .why{position:absolute;left:178px;top:709px;font-size:22px;font-weight:400;color:var(--blue)}
  .why-text{position:absolute;left:182px;top:747px;width:540px;font-size:12px;line-height:16px;color:var(--hot-pink)}

  .card-img{position:absolute;top:795px;width:131px;height:105px;border:1px solid #8a6f75;background:#fff;padding:3px}
  .card-img div{width:100%;height:100%}
  .card-title{position:absolute;top:799px;font-size:12px;font-weight:400;color:var(--brown-text)}
  .card-text{position:absolute;top:818px;width:145px;font-size:11px;line-height:16px;color:var(--brown-text)}

  .featured{position:absolute;left:760px;top:492px;width:266px;height:239px;background:var(--rose);border-radius:3px}
  .standard{position:absolute;left:760px;top:734px;width:266px;height:152px;background:var(--sky);border-radius:3px}
  .box-title{position:absolute;left:41px;font-size:22px;color:var(--white);font-weight:400}
  .box-rule{position:absolute;left:90px;top:13px;width:110px;height:1px;background:rgba(255,255,255,.6)}
  .featured .box-title{top:27px}
  .featured-text{position:absolute;left:41px;top:67px;width:225px;font-size:11.5px;line-height:16px;color:#1e1214}
  .featured-img{position:absolute;left:38px;top:113px;width:100px;height:110px;border-radius:45%;background:radial-gradient(circle at 50% 35%,#f4e2e4,#7a2a36 60%,#4a1c24)}
  .feature-links{list-style:none;position:absolute;left:158px;top:110px;width:90px}
  .feature-links li{font-size:11px;color:var(--white);height:22px;padding-top:2px;border-bottom:1px dashed rgba(255,255,255,.7)}
  .feature-links li:last-child{border-bottom:0}
  .standard .box-title{top:26px}
  .chef-img{position:absolute;left:40px;top:59px;width:90px;height:80px;border:2px solid #e9f1f6;background:linear-gradient(#8a6a4a,#d9c6b2)}
  .standard-text{position:absolute;left:137px;top:64px;width:120px;font-size:11px;line-height:16px;color:var(--white)}
  .more{position:absolute;left:140px;top:116px;font-size:11px;color:var(--white);text-decoration:underline}

  .connect{position:absolute;left:773px;top:906px;font-size:11px;color:#4b3a3d}
  .social{position:absolute;top:904px;width:20px;height:20px;border-radius:2px}

  .footer-band{position:absolute;left:45px;top:935px;width:1112px;height:66px;background:var(--choc-light)}
  .footer{position:absolute;left:147px;top:943px;width:906px;height:65px;background:var(--choc-dark);color:var(--white);text-align:center}
  .footer-links{margin-top:13px;font-size:12px}
  .footer-links span{margin:0 6px}
  .copyright{margin-top:8px;font-size:11px}
</style>
</head>
<body>
  <div class="page"></div>
  <div class="header-bg"></div>

  <form class="search">Search <input type="text" aria-label="Search"><button type="button">Go</button></form>

  <div class="nav-tail left"></div>
  <div class="nav-tail right"></div>
  <nav class="nav">
    <ul>
      <li class="active" style="left:120px">Home</li>
      <li style="left:214px">About Us</li>
      <li style="left:316px">Photo gallery</li>
      <li style="left:440px">Flavor Menu</li>
      <li style="left:563px">Products</li>
      <li style="left:660px">Contact</li>
      <li style="left:750px">Enquiry</li>
    </ul>
  </nav>

  <div class="logo">
    <span class="logo-dot"></span>
    <span class="logo-name">Velvet Ladle Wishes</span>
  </div>

  <svg class="scallop" width="910" height="90" viewBox="0 0 910 90" aria-hidden="true">
    <defs>
      <linearGradient id="bandFill" x1="0" y1="0" x2="0" y2="1">
        <stop offset="0" stop-color="#fcc9ce"/>
        <stop offset="1" stop-color="#f9b4bc"/>
      </linearGradient>
      <pattern id="scallopEdge" x="2" y="0" width="12" height="14" patternUnits="userSpaceOnUse">
        <path d="M0 0 q6 12 12 0 Z" fill="#fbd0d5" stroke="#f1a3ad" stroke-width="1"/>
      </pattern>
    </defs>
    <path d="M8 0 H902 L908 68 H2 Z" fill="url(#bandFill)"/>
    <rect x="2" y="68" width="906" height="10" fill="url(#scallopEdge)"/>
  </svg>
  <div class="hero-art" role="img" aria-label="Empty cupcake wrapper on a saucer with two cherries"></div>

  <main>
    <h1 class="welcome">Welcome to Velvet Ladle Wishes!</h1>
    <p class="lead-pink">These cases are perfectly simple and easy to distinguish.</p>
    <p class="lead-brown">The wise man therefore always holds in these matters to this principle of selection:</p>
    <p class="intro">These cases are perfectly simple and easy to distinguish. In a free hour, when our power of choice is untrammelled and when nothing prevents our being able to do what we like best, every pleasure is to be welcomed and every pain avoided. But in certain circumstances and owing to the claims of duty or the obligations of business it will frequently occur that pleasures have to be repudiated and annoyances accepted. The wise man therefore always holds in these matters to this principle of selection: he rejects pleasures to secure other greater pleasures, or else he endures pains to avoid worse pains</p>

    <h2 class="why">Why choose us our bakery?</h2>
    <p class="why-text">These cases are perfectly simple and easy to distinguish.n a free hour, when our power of choice is untrammelled and when nothing prevents</p>

    <div class="card-img" style="left:185px"><div role="img" aria-label="Tiered stand of pink decorated cupcakes" style="background:linear-gradient(#f3d2d8,#e46a86)"></div></div>
    <h3 class="card-title" style="left:323px">At vero eos et accusamus</h3>
    <p class="card-text" style="left:322px">Temporibus autem quibus-dam et aut officiis debitis aut rerum necessitatibus saepe eveniet ut et voluptates repudiandae .</p>

    <div class="card-img" style="left:470px"><div role="img" aria-label="Chocolate cupcake with white frosting and a butterfly topper" style="background:radial-gradient(circle at 50% 45%,#f4eee6,#c9b060 45%,#3a2418 80%)"></div></div>
    <h3 class="card-title" style="left:607px">At vero eos et accusamus</h3>
    <p class="card-text" style="left:606px">Temporibus autem quibus-dam et aut officiis debitis aut rerum necessitatibus saepe eveniet ut et voluptates repudiandae .</p>
  </main>

  <aside>
    <section class="featured">
      <div class="box-rule"></div>
      <h2 class="box-title">Featured Category</h2>
      <p class="featured-text">The wise man therefore always holds in these matters to this principle of selection:</p>
      <div class="featured-img" role="img" aria-label="Chocolate cupcake with a sprinkled flower topper"></div>
      <ul class="feature-links">
        <li>greater pleasures</li><li>greater pleasures</li><li>greater pleasures</li><li>greater pleasures</li><li>greater pleasures</li>
      </ul>
    </section>
    <section class="standard">
      <div class="box-rule"></div>
      <h2 class="box-title">Our Standard</h2>
      <div class="chef-img" role="img" aria-label="Portrait of the head baker"></div>
      <p class="standard-text">The wise man therefore always holds in these matters to this principle</p>
      <span class="more">more</span>
    </section>
    <span class="connect">Connect with us:</span>
    <div class="social" style="left:868px;background:#3b5a9a" aria-label="Social link"></div>
    <div class="social" style="left:895px;background:#6cc3e6" aria-label="Social link"></div>
    <div class="social" style="left:922px;background:#ee7a2f" aria-label="Social link"></div>
    <div class="social" style="left:948px;background:#1c76b0" aria-label="Social link"></div>
    <div class="social" style="left:975px;background:#5aa646" aria-label="Social link"></div>
  </aside>

  <div class="footer-band"></div>
  <footer class="footer">
    <div class="footer-links">Home<span>|</span>About Us<span>|</span>Photo gallery<span>|</span>Flavor Menu<span>|</span>Products<span>|</span>Contact<span>|</span>Enquiry</div>
    <div class="copyright">© copyrights velvet ladle wishes.All rights Reserved</div>
  </footer>
</body>
</html>
```